Product Designer Business Card

Small product design, engineering and prototyping firm in need of a clean, professional business card design. To support our 3D design and drawing services, we offer 3D printing, molding, and casting of plastics, silicones, resins, etc. Our logo can still be modified/changed if necessary. The red/orange color is preferred, but may be substituted with blue or green, potentially. Either way, the colour of the logo should be match/compliment colors used throughout the design. One thought is to have the logo/contact info on one side, with the other side describing services offered, like with a small icon of 3D printer, molding, casting, and computer with a 3D model on-screen.
Industry/Entity Type
Mechanical Engineering
Contact Information for Business Card
Company: Kelvar Design
Phone: 613-582-9047
Email: mark@kelvardesign.ca

```html
<!DOCTYPE html>
<html lang="en">
<head>
<meta charset="UTF-8">
<title>Kelvar Design – Business Card</title>
<link href="https://fonts.googleapis.com/css2?family=Montserrat:wght@400;500;600&display=swap" rel="stylesheet">
<style>
  :root {
    --bg: #dcdad8;
    --brand-red: #e02a0a;
    --brand-red-light: #ef5a3c;
    --deep-maroon: #4a0c07;
    --ink-dark: #3b0f0c;
    --ink-grey: #5d5d5d;
    --paper: #ffffff;
  }
  html, body {
    margin: 0;
    width: 1200px;
    height: 912px;
    overflow: hidden;
    background: var(--bg);
    font-family: "Montserrat", Arial, sans-serif;
  }
  .canvas {
    position: relative;
    width: 1200px;
    height: 912px;
  }
  .card {
    position: absolute;
    left: 250px;
    width: 700px;
    height: 400px;
    border-radius: 22px;
    overflow: hidden;
    box-shadow: 0 6px 18px rgba(0,0,0,0.18);
  }
  /* Services side */
  .card-services {
    top: 40px;
    background: var(--brand-red);
  }
  .service-list {
    position: absolute;
    left: 0; right: 0; top: 110px;
    display: flex;
    justify-content: center;
    gap: 60px;
  }
  .service {
    display: flex;
    flex-direction: column;
    align-items: center;
    width: 150px;
  }
  .service-icon {
    width: 130px;
    height: 130px;
    border-radius: 8px;
    background: var(--brand-red-light);
  }
  .service-label {
    margin-top: 14px;
    color: var(--paper);
    font-size: 22px;
    font-weight: 500;
  }
  /* Contact side */
  .card-contact {
    top: 472px;
    background: var(--paper);
  }
  .swoosh {
    position: absolute;
    left: 0; top: 0;
    width: 700px;
    height: 400px;
  }
  .brand {
    position: absolute;
    left: 0; right: 0; top: 60px;
    display: flex;
    justify-content: center;
    align-items: center;
    gap: 16px;
  }
  .brand-dot {
    width: 44px;
    height: 44px;
    border-radius: 50%;
    background: var(--brand-red);
  }
  .brand-name {
    font-size: 46px;
    font-weight: 600;
    letter-spacing: 6px;
    color: var(--ink-dark);
  }
  .contact-row {
    position: absolute;
    left: 0; right: 0; top: 172px;
    display: flex;
    justify-content: center;
    align-items: center;
  }
  .person {
    text-align: right;
    padding-right: 20px;
  }
  .person-name {
    color: var(--brand-red);
    font-size: 22px;
    font-weight: 500;
    line-height: 1.1;
  }
  .person-title {
    color: var(--ink-grey);
    font-size: 19px;
    line-height: 1.2;
  }
  .divider {
    width: 1.5px;
    height: 56px;
    background: var(--brand-red);
  }
  .details {
    padding-left: 20px;
    color: var(--ink-grey);
    font-size: 18px;
    line-height: 1.45;
  }
  .detail {
    display: flex;
    align-items: center;
    gap: 8px;
  }
  .detail svg { width: 14px; height: 14px; }
</style>
</head>
<body>
<main class="canvas">

  <section class="card card-services">
    <div class="service-list">
      <div class="service">
        <div class="service-icon" role="img" aria-label="Line icon of a molding press"></div>
        <span class="service-label">Molding</span>
      </div>
      <div class="service">
        <div class="service-icon" role="img" aria-label="Line icon of a 3D printer"></div>
        <span class="service-label">3D printer</span>
      </div>
      <div class="service">
        <div class="service-icon" role="img" aria-label="Line icon representing casting"></div>
        <span class="service-label">Casting</span>
      </div>
    </div>
  </section>

  <section class="card card-contact">
    <svg class="swoosh" viewBox="0 0 700 400" aria-hidden="true">
      <path d="M210 400 Q480 345 700 268 L700 400 Z" fill="var(--deep-maroon)"/>
      <path d="M210 400 Q480 345 700 268 L700 280 Q490 352 250 400 Z" fill="var(--brand-red)"/>
      <path d="M140 392 Q450 338 700 252" fill="none" stroke="var(--brand-red)" stroke-width="3"/>
    </svg>

    <div class="brand">
      <span class="brand-dot"></span>
      <span class="brand-name">Kelvar Design</span>
    </div>

    <div class="contact-row">
      <div class="person">
        <div class="person-name">ALDRIC PENFOLD</div>
        <div class="person-title">President</div>
      </div>
      <div class="divider"></div>
      <div class="details">
        <div class="detail">
          <svg viewBox="0 0 16 16" aria-hidden="true"><path d="M3 1.5l3 .5 1 3-1.8 1.3a9 9 0 0 0 4.5 4.5L11 9l3 1 .5 3-2 1.5C6.5 14 2 9.5 1.5 3.5Z" fill="var(--brand-red)"/></svg>
          <span>613-582-9047</span>
        </div>
        <div class="detail">
          <svg viewBox="0 0 16 16" aria-hidden="true"><rect x="1.5" y="3.5" width="13" height="9" fill="none" stroke="var(--brand-red)" stroke-width="1.6"/><path d="M1.5 3.5l6.5 5 6.5-5" fill="none" stroke="var(--brand-red)" stroke-width="1.6"/></svg>
          <span>mark@kelvardesign.ca</span>
        </div>
      </div>
    </div>
  </section>

</main>
</body>
</html>
```